Plumbing & Heating company

A leaflet containing -

Company name - Larkfield Plumbing Solutions
logo
Mobile number - 07700 914062
Landline - 01632 870215
Email - Info@larkfieldplumbing.example
website - Larkfield-plumbing.example
Social media logos - insta, Facebook

services we offer

- Boiler replacements (free quote)
- General plumbing & heating
- Tap replacements
- 1st & 2nd
- New builds & Extensions
- Cylinder replcemets

```html
<!DOCTYPE html>
<html lang="en">
<head>
<meta charset="utf-8">
<title>Larkfield Plumbing Solutions – Leaflet</title>
<link href="https://fonts.googleapis.com/css2?family=Bebas+Neue&family=Montserrat:wght@400;600;700;800;900&display=swap" rel="stylesheet">
<style>
  :root{
    --orange:#ec7a22;
    --orange-deep:#d9651a;
    --blue:#1d6db3;
    --blue-deep:#135a98;
    --charcoal:#3a3b3e;
    --charcoal-dark:#2c2d30;
    --white:#ffffff;
    --ink:#151515;
    --stage:#dcdcdc;
  }
  *{box-sizing:border-box;margin:0;padding:0}
  html,body{width:704px;height:1200px;overflow:hidden}
  body{background:var(--stage);font-family:'Montserrat',Arial,sans-serif;position:relative}
  .leaflet{position:absolute;left:12px;top:119px;width:680px;height:962px;background:var(--charcoal);overflow:hidden;box-shadow:0 6px 18px rgba(0,0,0,.18)}
  .leaflet > *{position:absolute}
  .backdrop{left:0;top:0;width:680px;height:600px}
  .brand{left:22px;top:44px;width:270px;display:flex;align-items:center;gap:10px}
  .brand-dot{width:22px;height:22px;border-radius:50%;background:var(--orange);flex:none}
  .brand-name{font-weight:800;font-size:24px;line-height:1.1;color:var(--blue);text-transform:uppercase;letter-spacing:.5px}
  .title{left:32px;top:214px;color:var(--white)}
  .title-light{font-weight:400;font-size:38px;line-height:1;letter-spacing:.5px}
  .title-bold{font-weight:700;font-size:35px;line-height:1.1;margin-top:4px}
  .title-tag{display:inline-block;margin-top:6px;background:var(--orange);border:2px solid #f39a50;font-size:19px;font-weight:400;padding:3px 16px;letter-spacing:.5px}
  .title-rule{left:34px;top:342px;width:280px;height:2px;background:#6a6b6e}
  .title-rule::before{content:"";position:absolute;left:0;top:-1px;width:76px;height:4px;background:var(--orange)}
  .gallery{top:359px;height:192px;background:linear-gradient(160deg,#e9e4dc,#b7a995)}
  .gallery-one{left:21px;width:116px;background:linear-gradient(160deg,#f2f2f0,#c9c6c0)}
  .gallery-two{left:148px;width:117px;background:linear-gradient(170deg,#d8bd92,#a98a60)}
  .gallery-three{left:275px;width:117px;background:linear-gradient(160deg,#d9d3c8,#a88f76)}
  .services-band{left:0;top:590px;width:680px;height:201px;background:linear-gradient(180deg,var(--orange),var(--orange-deep))}
  .services-tab{left:0;top:560px;height:60px;width:265px;background:var(--blue-deep);clip-path:polygon(0 0,100% 0,94% 100%,0 100%);color:var(--white);font-family:'Bebas Neue',Impact,sans-serif;font-size:31px;padding:14px 0 0 31px;letter-spacing:.3px}
  .service-list{list-style:none}
  .service-list li{display:flex;align-items:center;gap:12px;color:var(--white);font-weight:600;font-size:15px;line-height:1.2;height:36px;border-bottom:1px solid rgba(255,255,255,.35)}
  .service-list li:last-child{border-bottom:none}
  .service-left{left:30px;top:636px;width:310px}
  .service-right{left:365px;top:636px;width:292px}
  .service-left li:first-child{height:48px}
  .service-icon{width:30px;height:30px;border-radius:50%;background:var(--ink);border:2px solid #f7a25e;flex:none;display:flex;align-items:center;justify-content:center}
  .service-icon::after{content:"";width:8px;height:8px;border-radius:50%;background:var(--orange)}
  .contact-band{left:0;top:791px;width:680px;height:96px;background:var(--white)}
  .cta{left:34px;top:806px;line-height:1}
  .cta-top{color:var(--orange);font-weight:800;font-size:27px}
  .cta-main{color:var(--ink);font-weight:900;font-size:40px;letter-spacing:-.5px}
  .phone-badge{top:827px;width:44px;height:44px;border-radius:50%;border:3px solid var(--blue);background:var(--white);display:flex;align-items:center;justify-content:center;box-shadow:0 0 0 3px #d9e7f4}
  .phone-mobile{left:209px}
  .phone-landline{left:438px}
  .contact-label{top:817px;font-weight:800;font-size:22px;color:var(--ink)}
  .label-mobile{left:274px}
  .label-landline{left:503px}
  .contact-number{top:842px;height:32px;border-radius:16px;background:var(--orange);color:var(--white);font-weight:800;font-size:21px;display:flex;align-items:center;justify-content:center;box-shadow:0 2px 0 #b55213}
  .number-mobile{left:261px;width:170px}
  .number-landline{left:491px;width:168px}
  .footer-pill{left:0;top:902px;width:505px;height:34px;border-radius:0 17px 17px 0;background:var(--orange);display:flex;align-items:center;color:var(--white);font-size:12px;font-weight:600}
  .footer-icon{width:26px;height:26px;border-radius:50%;background:var(--ink);border:2px solid #f7a25e;display:flex;align-items:center;justify-content:center;flex:none}
  .footer-email{margin-left:44px}
  .footer-web{margin-left:20px}
  .footer-pill span{margin-left:12px}
  .social{top:898px;width:42px;height:42px;border-radius:50%;background:var(--white);border:3px solid var(--blue);box-shadow:0 0 0 3px #cfe0f1}
  .social-one{left:535px}
  .social-two{left:595px}
</style>
</head>
<body>
<main class="leaflet">
  <svg class="backdrop" viewBox="0 0 680 600" aria-hidden="false">
    <defs>
      <linearGradient id="portraitTone" x1="0" y1="0" x2="1" y2="1">
        <stop offset="0" stop-color="#bfc1c3"/>
        <stop offset=".55" stop-color="#6d7f9c"/>
        <stop offset="1" stop-color="#3f4f6f"/>
      </linearGradient>
    </defs>
    <path d="M0 -10 H400 C345 55 308 125 298 196 C200 176 100 160 0 166 Z" fill="#ffffff" stroke="#1d6db3" stroke-width="5"/>
    <path d="M392 -10 C300 80 250 300 330 480 C385 565 520 600 690 592 L690 -10 Z" fill="#1d6db3"/>
    <path role="img" aria-label="Photo of a plumber holding hoses and a tool bag in a plant room" d="M400 -10 C312 80 264 300 342 474 C395 552 525 586 690 580 L690 -10 Z" fill="url(#portraitTone)"/>
  </svg>

  <div class="brand">
    <span class="brand-dot"></span>
    <span class="brand-name">Larkfield Plumbing Solutions</span>
  </div>

  <h1 class="title">
    <div class="title-light">LARKFIELD</div>
    <div class="title-bold">PLUMBING</div>
    <div class="title-tag">SOLUTIONS</div>
  </h1>
  <div class="title-rule"></div>

  <div class="gallery gallery-one" role="img" aria-label="Photo of an installed hot water cylinder and wall boiler"></div>
  <div class="gallery gallery-two" role="img" aria-label="Photo of a boiler fitted in a timber cupboard"></div>
  <div class="gallery gallery-three" role="img" aria-label="Photo of copper pipework in a new build"></div>

  <div class="services-band"></div>
  <h2 class="services-tab">SERVICES WE OFFER</h2>

  <ul class="service-list service-left">
    <li><i class="service-icon"></i>BOILER REPLACEMENTS<br>(FREE QUOTE)</li>
    <li><i class="service-icon"></i>GENERAL PLUMBING &amp; HEATING</li>
    <li><i class="service-icon"></i>TAP REPLACEMENTS</li>
  </ul>
  <ul class="service-list service-right">
    <li><i class="service-icon"></i>1ST &amp; 2ND</li>
    <li><i class="service-icon"></i>NEW BUILDS &amp; EXTENSIONS</li>
    <li><i class="service-icon"></i>CYLINDER REPLCEMETS</li>
  </ul>

  <div class="contact-band"></div>
  <div class="cta"><div class="cta-top">GIVE US</div><div class="cta-main">A CALL</div></div>

  <div class="phone-badge phone-mobile">
    <svg width="22" height="22" viewBox="0 0 24 24"><path fill="#1d6db3" d="M6.6 10.8a15 15 0 0 0 6.6 6.6l2.2-2.2c.3-.3.7-.4 1-.2 1.1.4 2.3.6 3.6.6.6 0 1 .4 1 1V20c0 .6-.4 1-1 1A17 17 0 0 1 3 4c0-.6.4-1 1-1h3.5c.6 0 1 .4 1 1 0 1.3.2 2.5.6 3.6.1.3 0 .7-.2 1z"/></svg>
  </div>
  <div class="contact-label label-mobile">Mobile</div>
  <div class="contact-number number-mobile">07700-914062</div>

  <div class="phone-badge phone-landline">
    <svg width="22" height="22" viewBox="0 0 24 24"><path fill="#1d6db3" d="M6.6 10.8a15 15 0 0 0 6.6 6.6l2.2-2.2c.3-.3.7-.4 1-.2 1.1.4 2.3.6 3.6.6.6 0 1 .4 1 1V20c0 .6-.4 1-1 1A17 17 0 0 1 3 4c0-.6.4-1 1-1h3.5c.6 0 1 .4 1 1 0 1.3.2 2.5.6 3.6.1.3 0 .7-.2 1z"/></svg>
  </div>
  <div class="contact-label label-landline">Landline</div>
  <div class="contact-number number-landline">01632-870215</div>

  <div class="footer-pill">
    <i class="footer-icon footer-email">
      <svg width="12" height="12" viewBox="0 0 24 24"><rect x="2" y="5" width="20" height="14" rx="2" fill="none" stroke="#fff" stroke-width="2.5"/><path d="M2 6l10 7 10-7" fill="none" stroke="#fff" stroke-width="2.5"/></svg>
    </i>
    <span>Info@larkfieldplumbing.example</span>
    <i class="footer-icon footer-web">
      <svg width="12" height="12" viewBox="0 0 24 24"><circle cx="12" cy="12" r="9" fill="none" stroke="#fff" stroke-width="2.5"/><path d="M3 12h18M12 3c3 3 3 15 0 18M12 3c-3 3-3 15 0 18" fill="none" stroke="#fff" stroke-width="2"/></svg>
    </i>
    <span>Larkfield-plumbing.example</span>
  </div>

  <a class="social social-one" aria-label="Social media profile"></a>
  <a class="social social-two" aria-label="Social media profile"></a>
</main>
</body>
</html>
```